Harborline LLC
256-418-7305
438 Walt R. Pemberton Blvd.
Sylacauga, AL 35150
harborlinellc97@quilmail.example

Heavy& Light Duty Diesel Truck, Trailer, and Equipment Repair
Certified NMC Master Tech & trained techs

Services:
alignments, brakes, suspension, A/C, engine overhauls, DOT inspections, fleet maintenance, computer diagnosis for gas & diesel, warranty work, performance parts for all diesel pickups, Welding & fabrication

Colors, text for Company, phone number, email address in bright red, all other text black.
background color of postcard light grey, black border around pictures.

Industry/Entity Type

Computer

Colors
ec2027

```html
<!DOCTYPE html>
<html lang="en">
<head>
<meta charset="utf-8">
<title>Harborline LLC – Premiere Truck Repair</title>
<link rel="stylesheet" href="https://fonts.googleapis.com/css2?family=Arimo:wght@400;700&family=Roboto+Condensed:wght@700&display=swap">
<style>
  :root {
    --brand-red: #ec2027;
    --ink: #111111;
    --card-light: #f1f1f1;
    --card-mid: #c9c9c9;
    --card-dark: #a9a9a9;
    --band-dark: #2b2b2b;
    --band-mid: #555555;
    --band-text: #cfcfcf;
    --page-bg: #e6e4e0;
  }
  * { box-sizing: border-box; margin: 0; padding: 0; }
  html, body {
    width: 1200px; height: 924px; overflow: hidden;
    background: var(--page-bg);
  }
  .postcard {
    position: absolute; left: 30px; top: 42px;
    width: 1140px; height: 840px;
    background: linear-gradient(160deg, var(--card-light) 0%, var(--card-mid) 35%, var(--card-light) 55%, var(--card-dark) 80%, var(--card-light) 100%);
    font-family: "Arimo", Arial, sans-serif;
    color: var(--ink);
    text-align: center;
  }
  .masthead {
    position: absolute; left: 44px; top: 30px; right: 44px;
    display: flex; align-items: baseline; gap: 22px;
    padding-bottom: 6px;
    border-bottom: 3px solid var(--ink);
  }
  .company-name {
    font-weight: 700; font-size: 78px; line-height: 1;
    color: var(--brand-red); letter-spacing: 2px;
  }
  .tagline { font-weight: 700; font-size: 38px; }
  .intro {
    position: absolute; left: 0; right: 0; top: 150px;
    font-weight: 700; font-size: 27px; line-height: 36px; letter-spacing: 0.5px;
  }
  .gallery {
    position: absolute; left: 44px; right: 44px; top: 240px; height: 214px;
    display: flex; gap: 8px;
  }
  .gallery .photo {
    flex: 1; border: 3px solid var(--ink);
  }
  .photo-shop { background: linear-gradient(135deg, #3a4e74 0%, #7d8ea8 50%, #2c2f38 100%); }
  .photo-scan { background: linear-gradient(135deg, #26272b 0%, #6b4b3c 45%, #9c3d33 60%, #1e1f22 100%); }
  .photo-garage { background: linear-gradient(180deg, #7fa0c8 0%, #a9b7bf 40%, #8c6b4f 75%, #6f6a5e 100%); }
  .services-band {
    position: absolute; left: 44px; right: 44px; top: 462px; height: 46px;
    background: linear-gradient(180deg, var(--band-mid), var(--band-dark));
    color: var(--band-text);
    font-weight: 700; font-size: 26px; line-height: 46px; letter-spacing: 9px;
  }
  .services-list {
    position: absolute; left: 0; right: 0; top: 518px;
    font-family: "Roboto Condensed", "Arial Narrow", sans-serif;
    font-weight: 700; font-size: 26px; line-height: 32px;
  }
  .contact { position: absolute; left: 0; right: 0; top: 622px; color: var(--brand-red); font-weight: 700; }
  .hours { font-family: "Roboto Condensed", "Arial Narrow", sans-serif; font-size: 28px; line-height: 40px; }
  .hours strong { font-size: 30px; }
  .phone { font-size: 50px; line-height: 60px; letter-spacing: 1px; }
  .address { font-size: 29px; line-height: 36px; }
  .email { font-size: 23px; line-height: 32px; }
</style>
</head>
<body>
  <main class="postcard">
    <header class="masthead">
      <h1 class="company-name">Harborline LLC</h1>
      <p class="tagline">Premiere Truck Repair</p>
    </header>

    <div class="intro">
      <p>Heavy&amp; Light Duty Diesel Truck, Trailer, and Equipment Repair</p>
      <p>Certified NMC Master Tech &amp; trained techs</p>
    </div>

    <section class="gallery">
      <div class="photo photo-shop" role="img" aria-label="Semi truck parked inside a repair shop bay"></div>
      <div class="photo photo-scan" role="img" aria-label="Technician holding a diagnostic scan tablet"></div>
      <div class="photo photo-garage" role="img" aria-label="Shop building with service pickup trucks outside"></div>
    </section>

    <h2 class="services-band">SERVICES:</h2>

    <div class="services-list">
      <p>Alignments • Brakes • Suspension • A/C • Engine Overhauls • Dot Inspections</p>
      <p>Fleet Maintenance • Computer Diagnosis For Gas &amp; Diesel • Warranty Work</p>
      <p>Performance Parts For All Diesel Pickups • Welding &amp; Fabrication</p>
    </div>

    <footer class="contact">
      <p class="hours">Working hours: <strong>Monday-Friday 7am - 4pm</strong></p>
      <p class="phone">256.418.7305</p>
      <p class="address">438 Walt R. Pemberton Blvd. Sylacauga, AL 35150</p>
      <p class="email">harborlinellc97@quilmail.example</p>
    </footer>
  </main>
</body>
</html>
```